Brindlewick Solutions Ltd

I'd like to create a company letterhead for the attached logo in word format.

I'd like to emphasis the icon in large translucent state from the left corner and ensure that the letterhead colouring matches the colour palette of the current logo with a contrast so it's clear to see. I've attached a copy of our sister company page on the app for reference.

```html
<!DOCTYPE html>
<html lang="en">
<head>
<meta charset="utf-8">
<title>Brindlewick Solutions Ltd — Letterhead</title>
<link href="https://fonts.googleapis.com/css2?family=Lato:wght@400;700&display=swap" rel="stylesheet">
<style>
  :root {
    --backdrop: #8a8a8a;
    --ink: #111111;
    --paper: #ffffff;
    --on-ink: #f2f2f2;
  }
  * { box-sizing: border-box; margin: 0; padding: 0; }
  html, body {
    width: 1061px; height: 1200px; overflow: hidden;
    background: var(--backdrop);
    font-family: "Lato", sans-serif;
  }
  .letterhead {
    position: absolute; left: 120px; top: 20px;
    width: 820px; height: 1160px;
    background: var(--paper);
  }
  .letterhead__bands { position: absolute; inset: 0; }
  .brand {
    position: absolute; top: 42px; left: 0; width: 100%;
    display: flex; justify-content: center; align-items: center; gap: 12px;
    color: var(--on-ink);
  }
  .brand__mark {
    width: 50px; height: 50px; border-radius: 50%;
    background: var(--on-ink);
  }
  .brand__name {
    font-size: 30px; font-weight: 400; letter-spacing: 0.3px;
  }
  .contact {
    position: absolute; left: 0; width: 100%; top: 1072px;
    text-align: center; color: var(--on-ink);
    font-size: 13px; line-height: 22px;
  }
  .contact__company { font-weight: 700; }
  .contact__line { display: flex; justify-content: center; align-items: center; gap: 6px; }
  .contact__item { display: inline-flex; align-items: center; gap: 4px; }
  .contact__item svg { width: 11px; height: 11px; fill: var(--on-ink); }
  .contact__web { letter-spacing: 3px; font-size: 13px; }
  .contact__web strong { font-weight: 700; }
</style>
</head>
<body>
  <div class="letterhead">
    <svg class="letterhead__bands" viewBox="0 0 820 1160" width="820" height="1160" aria-hidden="true">
      <path fill="var(--ink)" d="M0 0 H820 V206 C700 152 570 126 446 126 C300 126 150 158 0 199 Z"/>
      <path fill="var(--ink)" d="M0 971 C120 1030 260 1052 387 1052 C540 1052 700 1012 820 978 V1160 H0 Z"/>
    </svg>

    <div class="brand">
      <span class="brand__mark"></span>
      <span class="brand__name">Brindlewick Solutions Ltd</span>
    </div>

    <div class="contact">
      <p><span class="contact__company">Brindlewick Solutions Ltd</span> | 418 Harrowgate Lane | Millbrook, CT 06422</p>
      <p class="contact__line">
        <span class="contact__item">
          <svg viewBox="0 0 12 12"><path d="M2.5 0.5 L4.5 0.5 L5.3 3 L4 4.2 C4.6 5.6 6.2 7.3 7.8 8 L9 6.7 L11.5 7.5 L11.5 9.5 C11.5 10.8 10.5 11.6 9 11.4 C4.8 10.6 1.4 7.2 0.6 3 C0.4 1.5 1.2 0.5 2.5 0.5 Z"/></svg>
          (555) 014-2290
        </span>
        <span class="contact__item">
          <svg viewBox="0 0 12 12"><path d="M3 0 H9 V12 H3 Z M4 1.5 V9.5 H8 V1.5 Z M5.5 10.2 H6.5 V11.2 H5.5 Z"/></svg>
          (555) 014-2291
        </span>
        <span class="contact__item">
          <svg viewBox="0 0 12 12"><path d="M3 0 H9 V3 H11 C11.6 3 12 3.4 12 4 V9 H9.5 V12 H2.5 V9 H0 V4 C0 3.4 0.4 3 1 3 H3 Z M4 1 V3 H8 V1 Z M3.5 7.5 V11 H8.5 V7.5 Z"/></svg>
          (555) 014-2292
        </span>
        <span class="contact__item">
          <svg viewBox="0 0 12 12"><path d="M0 2 H12 V3 L6 7 L0 3 Z M0 4.2 L6 8.2 L12 4.2 V10 H0 Z"/></svg>
          info@brindlewicksolutions.com
        </span>
      </p>
      <p class="contact__web">WWW.<strong>BRINDLEWICKSOLUTIONS</strong>.COM</p>
    </div>
  </div>
</body>
</html>
```